Yacht, Boats, Watersports company needs a redesign of business card

Hello Designers!
We are a Boat dealership company that sells fun in the water, we sell boats, Yachts, Kayaks and also yacht WaterSport toys. We are looking to redesign our business cards in to something a little bit more sophisticated. in a way that we can make better use of our company colors. I'm attaching a zipped file containing the company 3 sets of company logo which one is an horizontal another one is a vertical and also a chromed 3d logo. Also is included two set of business cards that we use and also some designs that i think it's interesting. We use PMS 2026c Orange and PMS 7687C Blue. I would like to see at least two different options with the orange as accent and also using blue as an accent color. It's really important for the business cards to have a font option and size that is legible to most people. Our current website is wwww.coralpennant.com. Please visit if you want to have a better feeling of the Boat dealership
You can send Single sided or double side options. We are now using single sided but we may be open for a double side option if we really like the design.
Target Market(s)
Marine, boat sales, yacht sales, water toys sales/
Contact Information for Business Card
Name: Dale Whitcombe
Address: 212 North Fenwick Lane,
Gull Harbor, FL 34761
Phone: 727-731-8842
Fax: 727:731-8843
Cell: 727-382-1490
Email: dw@coralpennant.com
Website: coralpennant.com
Requirements
Must have
- the current information of the business card provided.
logo
use the PMS Colors
Nice to have
- a touch of elegance and sophistication but simple
Should not have
- should not have any typography that is hard to read, the card should be simple but yet sophisticated.

```html
<!DOCTYPE html>
<html lang="en">
<head>
<meta charset="utf-8">
<title>Coral Pennant – Business Card</title>
<link rel="stylesheet" href="https://fonts.googleapis.com/css2?family=Krona+One&family=Arimo:wght@400;500&display=swap">
<style>
  :root {
    --backdrop: #2e2f31;
    --brand-blue: #0f4a86;
    --brand-blue-deep: #0c3f74;
    --brand-orange: #f05a22;
    --card-white: #ffffff;
    --ink: #222428;
    --rule: #9a9a9a;
  }
  * { margin: 0; padding: 0; box-sizing: border-box; }
  html, body { width: 1200px; height: 1015px; overflow: hidden; }
  body {
    background: var(--backdrop);
    position: relative;
    font-family: "Arimo", Arial, sans-serif;
  }
  .card {
    position: absolute;
    left: 270px;
    width: 660px;
    height: 377px;
    box-shadow: 0 14px 30px rgba(0,0,0,.45);
  }
  /* back side */
  .card--back { top: 95px; background: var(--brand-blue); }
  .card--back .pattern-field {
    position: absolute; inset: 0;
    background: radial-gradient(circle at 50% 50%, var(--brand-blue) 0%, var(--brand-blue-deep) 100%);
  }
  .card--back .wordmark {
    position: absolute; left: 0; right: 0; top: 50%;
    transform: translateY(-50%);
    display: flex; flex-direction: column; align-items: center; gap: 16px;
  }
  .wordmark-dot {
    width: 46px; height: 46px; border-radius: 50%;
    border: 3px solid var(--card-white);
  }
  .wordmark-name {
    font-family: "Krona One", sans-serif;
    font-size: 26px; letter-spacing: 1px;
    color: var(--card-white);
    white-space: nowrap;
  }
  /* front side */
  .card--front { top: 540px; background: var(--card-white); }
  .front-logo {
    position: absolute; left: 0; width: 330px; top: 50%;
    transform: translateY(-50%);
    display: flex; flex-direction: column; align-items: center; gap: 16px;
  }
  .front-logo .wordmark-dot { border-color: var(--brand-orange); width: 62px; height: 62px; border-width: 4px; }
  .front-logo .wordmark-name { color: var(--brand-blue); font-size: 20px; }
  .divider {
    position: absolute; left: 340px; top: 70px; width: 1px; height: 237px;
    background: var(--rule);
  }
  .contact { position: absolute; left: 368px; top: 66px; }
  .person-name {
    font-family: "Krona One", sans-serif;
    font-weight: 400;
    font-size: 22px; white-space: nowrap; margin-bottom: 16px;
  }
  .person-name .first { color: var(--brand-blue); }
  .person-name .last { color: var(--brand-orange); }
  .contact-list { list-style: none; }
  .contact-list li {
    display: flex; align-items: center; gap: 10px;
    font-size: 15px; line-height: 25px; color: var(--ink);
    white-space: nowrap;
  }
  .contact-list svg { width: 14px; height: 14px; fill: var(--brand-blue); flex: none; }
  .web-domain { color: var(--brand-blue); }
  .address { margin-top: 16px; margin-left: 24px; font-size: 16px; line-height: 22px; color: var(--ink); font-style: normal; }
</style>
</head>
<body>

<section class="card card--back" aria-label="Card back">
  <div class="pattern-field" role="img" aria-label="Faint repeating brand emblem pattern on blue"></div>
  <div class="wordmark">
    <span class="wordmark-dot"></span>
    <span class="wordmark-name">CORAL PENNANT</span>
  </div>
</section>

<section class="card card--front" aria-label="Card front">
  <div class="front-logo">
    <span class="wordmark-dot"></span>
    <span class="wordmark-name">CORAL PENNANT</span>
  </div>
  <div class="divider"></div>
  <div class="contact">
    <h1 class="person-name"><span class="first">DALE</span> <span class="last">WHITCOMBE</span></h1>
    <ul class="contact-list">
      <li><svg viewBox="0 0 16 16"><path d="M3 1l3 3-1.5 2a9 9 0 005.5 5.5L12 10l3 3-2 2C6 15 1 10 1 3z"/></svg><span>727-731-8842</span></li>
      <li><svg viewBox="0 0 16 16"><path d="M4 1h7v4H4zM1 6h14v6h-3v3H4v-3H1zM5 10v4h6v-4z"/></svg><span>727:731-8843</span></li>
      <li><svg viewBox="0 0 16 16"><path d="M4 0h8a1 1 0 011 1v14a1 1 0 01-1 1H4a1 1 0 01-1-1V1a1 1 0 011-1zm1 2v10h6V2zm3 11a1 1 0 100 2 1 1 0 000-2z"/></svg><span>727-382-1490</span></li>
      <li><svg viewBox="0 0 16 16"><path d="M0 3h16v10H0zm1 1l7 5 7-5z" fill-rule="evenodd"/></svg><span>dw@coralpennant.com</span></li>
      <li><svg viewBox="0 0 16 16"><path d="M8 0a8 8 0 110 16A8 8 0 018 0zM2 7h3a13 13 0 011-5A6 6 0 002 7zm4 0h4a12 12 0 00-2-5 12 12 0 00-2 5zm5 0h3a6 6 0 00-4-5 13 13 0 011 5zM2 9a6 6 0 004 5 13 13 0 01-1-5zm4 0a12 12 0 002 5 12 12 0 002-5zm5 0a13 13 0 01-1 5 6 6 0 004-5z"/></svg><span>www.<span class="web-domain">coralpennant</span>.com</span></li>
    </ul>
    <address class="address">212 North Fenwick Lane<br>Gull Harbor, FL 34761</address>
  </div>
</section>

</body>
</html>
```